Looking for a cool, modern Cannabis Jar Label

I want you to come up with a better, modern look for a label.

I need it sized to 4” x 3” - I plan to print directly to label printer.

I want you to use Photoshop and deliver me a layered PSD file that I can edit and modify the information as needed..

The label information will need to include places for:
(1) Strain Name - most important part of label - larger font size than rest - example Kestrel Mist, PLV #7, Juniper Hollow
(2) Pricing - for Gram, 1/8, 1/4, 1/2. and Ounce
(3) Strain Designation (Hybrid, Indica or Sativa) - maybe color coded, different color for Indica v. Sativa, just an idea
(4) THC and CBD percentages - for example 23% THC and 0.05% CBD
(5) Farm name - a place where we can add the name/logo of the business that produced the product. example - Ovenrow Farms

I have attached a simple mockup showing the information.

I have also attached a few samples of labels we like to give you an idea of the look and feel we are going for.

I am wanting a very clean, modern, classy, readable look.The font will use is Gotham Font.

HI Everyone! Thank you for all of your designs. I am requesting an extension because I need more time to give adequate feedback to the designers. Thank you for your participation and all of your efforts! I will be making a decision soon!

• Gotham Font

• Thank you for your designs. I am sorry i have been slow in providing feedback, things have been really busy around here!
• I wanted to give some group general feedback. After reviewing all of the designs, there is a common theme among all of the designs that I would like to see changed.
• I would like to see the per gram pricing more prominent on the label. This is what most people are looking for when they are purchasing the product. So I would like to see this stand out from the other pricing tiers. As I think about it, they don't all need to be grouped together in a line. You could have the Per Gram pricing front and center some where and then the other pricing tiers grouped together somewhere else on the label.
• This is the order of importance of items on the label. Items at the the top of the list should be bigger than those below it.
• 1. Strain name
• 2. Pricing - being per gram the most important of all prices
• 3. THC/CBD percentages
• 4. Strain Type (indica, sativa, hybrid)
• 5. Farm name/logo
• When laying out these labels, they will be going on rounded jars and they will be on display. Think of jars with fancy labels in a candy store. They need to be eye catchy, appealing, but easy read.
• Thank you for all of your hard work, everyone is doing a great job.
• Best,
• Neta

```html
<!DOCTYPE html>
<html lang="en">
<head>
<meta charset="utf-8">
<title>Kestrel Mist – Jar Label</title>
<link href="https://fonts.googleapis.com/css2?family=Montserrat:wght@300;400;500;800&display=swap" rel="stylesheet">
<style>
  :root {
    --gold: #f8c12c;
    --gold-deep: #f5b800;
    --gold-pale: #f6e4a8;
    --gold-soft: #fbeec4;
    --tan: #dcc46c;
    --frame: #f6cd4c;
    --ink: #111111;
    --paper: #ffffff;
  }
  * { margin: 0; padding: 0; box-sizing: border-box; }
  html, body {
    width: 1200px; height: 917px; overflow: hidden; background: var(--paper);
  }
  .label {
    position: absolute; left: 0; top: 0;
    width: 1280px; height: 978px;
    transform: scale(0.9375); transform-origin: 0 0;
    font-family: "Montserrat", Arial, sans-serif;
    color: var(--ink);
  }
  .label__frame {
    position: absolute; left: 35px; top: 35px; width: 1200px; height: 900px;
    border: 6px solid var(--frame); background: var(--paper);
  }

  /* Header */
  .strain {
    position: absolute; left: 41px; top: 41px; width: 1024px; height: 267px;
    background: linear-gradient(90deg,
      var(--gold) 0%, var(--gold-deep) 8%, var(--gold-pale) 22%, var(--gold) 30%,
      var(--gold-pale) 40%, var(--gold) 48%, var(--gold-soft) 58%, var(--gold) 66%,
      var(--gold-pale) 76%, var(--gold-soft) 88%, var(--gold) 100%);
  }
  .strain__name, .strain__cross {
    position: absolute; left: 40px; font-weight: 400; line-height: 1;
    text-shadow: 2px 3px 4px rgba(0,0,0,.35);
    white-space: nowrap;
  }
  .strain__name { top: 60px; font-size: 118px; letter-spacing: 1px; }
  .strain__cross { top: 190px; font-size: 88px; }
  .strain__type {
    position: absolute; left: 1065px; top: 41px; width: 164px; height: 267px;
    background: var(--gold-pale);
  }
  .strain__type span {
    position: absolute; left: 50%; top: 50%;
    transform: translate(-50%, -50%) rotate(-90deg);
    font-size: 58px; font-weight: 300;
  }

  /* Pricing */
  .prices { position: absolute; left: 41px; top: 330px; width: 1188px; height: 320px; }
  .tier {
    position: absolute; top: 0; height: 318px;
    border-right: 4px solid var(--gold-soft); border-bottom: 4px solid var(--gold-soft);
  }
  .tier__price {
    position: absolute; top: 30px; left: 0; right: 0; text-align: center;
    font-size: 88px; font-weight: 300; line-height: 1;
  }
  .tier__unit {
    position: absolute; top: 152px; left: 50%; margin-left: -70px;
    width: 140px; height: 140px; border-radius: 50%;
    display: flex; align-items: center; justify-content: center;
    font-size: 66px; font-weight: 300;
  }
  .tier--gram  { left: 0;   width: 193px; }
  .tier--eighth{ left: 218px; width: 188px; }
  .tier--quarter{ left: 430px; width: 194px; }
  .tier--half  { left: 648px; width: 238px; }
  .tier--ounce { left: 908px; width: 260px; }
  .tier--gram .tier__unit   { background: linear-gradient(90deg, var(--gold) 20%, var(--gold-pale) 75%); }
  .tier--eighth .tier__unit { background: linear-gradient(90deg, var(--gold) 30%, var(--gold-deep) 55%, var(--gold-pale) 85%); }
  .tier--quarter .tier__unit{ background: linear-gradient(90deg, var(--gold-pale), var(--gold) 90%); }
  .tier--half .tier__unit   { background: linear-gradient(90deg, var(--gold) 60%, var(--gold-pale)); }
  .tier--ounce .tier__unit  { background: var(--gold); }

  /* Potency */
  .potency { position: absolute; left: 41px; top: 675px; width: 820px; height: 255px; }
  .potency svg { position: absolute; inset: 0; }
  .potency__label {
    position: absolute; top: 32px; font-size: 58px; font-weight: 800; line-height: 1;
  }
  .potency__value {
    position: absolute; top: 145px; font-size: 100px; font-weight: 400; line-height: 1;
    text-shadow: 1px 2px 3px rgba(0,0,0,.3);
  }
  .potency__value sup { font-size: 44px; vertical-align: 40px; }
  .potency--thc-label { left: 85px; }
  .potency--thc-value { left: 85px; }
  .potency--cbd-label { left: 535px; }
  .potency--cbd-value { left: 480px; }

  /* Grower */
  .grower { position: absolute; left: 866px; top: 675px; width: 363px; height: 255px; }
  .grower__title {
    height: 60px; background: var(--tan); text-align: center;
    font-size: 42px; font-weight: 400; line-height: 58px; letter-spacing: 1px;
  }
  .grower__mark {
    display: flex; align-items: center; gap: 18px; padding: 0 20px; height: 195px;
  }
  .grower__dot {
    width: 90px; height: 90px; border-radius: 50%; border: 3px solid var(--ink); flex: none;
  }
  .grower__name { font-size: 38px; font-weight: 500; line-height: 1.05; }
</style>
</head>
<body>
<div class="label">
  <div class="label__frame"></div>

  <header class="strain">
    <h1 class="strain__name">Kestrel Mist</h1>
    <h2 class="strain__cross">Juniper Hollow</h2>
  </header>
  <div class="strain__type"><span>Hybrid</span></div>

  <section class="prices">
    <div class="tier tier--gram"><div class="tier__price">$10</div><div class="tier__unit">g.</div></div>
    <div class="tier tier--eighth"><div class="tier__price">$35</div><div class="tier__unit">1/8</div></div>
    <div class="tier tier--quarter"><div class="tier__price">$70</div><div class="tier__unit">1/4</div></div>
    <div class="tier tier--half"><div class="tier__price">$140</div><div class="tier__unit">1/2</div></div>
    <div class="tier tier--ounce"><div class="tier__price">$280</div><div class="tier__unit">Oz</div></div>
  </section>

  <section class="potency">
    <svg width="820" height="255" viewBox="0 0 820 255" aria-hidden="true">
      <rect x="0" y="0" width="820" height="125" fill="var(--gold)"/>
      <polygon points="320,0 460,0 390,125" fill="var(--paper)"/>
      <polygon points="390,125 320,255 460,255" fill="var(--tan)"/>
    </svg>
    <div class="potency__label potency--thc-label">THC</div>
    <div class="potency__label potency--cbd-label">CBD</div>
    <div class="potency__value potency--thc-value">28<sup>%</sup></div>
    <div class="potency__value potency--cbd-value">0.05<sup>%</sup></div>
  </section>

  <section class="grower">
    <div class="grower__title">Grown by</div>
    <div class="grower__mark">
      <div class="grower__dot"></div>
      <div class="grower__name">Ovenrow Farms</div>
    </div>
  </section>
</div>
</body>
</html>
```